business card deign

Logo needs the following on it.
1. attached logo
2. Tagline - "Chilled coolers and loud speakers...we bring the fun!"
3. Name- Dalton Pikes, Founder and CPO
4. Address - 412 E. Carver Avenue, Ste 2207, Tampa, FL. 33917
5. Phone - 555.318.4726

```html
<!DOCTYPE html>
<html lang="en">
<head>
<meta charset="utf-8">
<title>Brimley Business Card</title>
<link rel="stylesheet" href="https://fonts.googleapis.com/css2?family=Open+Sans:wght@400;600&family=Roboto:wght@500;700;900&display=swap">
<style>
  :root {
    --stage: #232323;
    --card-black: #141414;
    --band-black: #1a1a1a;
    --paper: #ffffff;
    --ink: #0d0d0d;
  }
  * { box-sizing: border-box; margin: 0; padding: 0; }
  html, body { width: 1200px; height: 780px; overflow: hidden; background: var(--stage); }
  .stage { position: relative; width: 1200px; height: 780px; }

  .card {
    position: absolute;
    width: 560px; height: 320px;
    border-radius: 22px;
    overflow: hidden;
    box-shadow: 0 14px 30px rgba(0,0,0,.55);
  }

  /* Back side */
  .card-back { left: 50px; top: 50px; background: var(--card-black); }
  .back-pattern {
    position: absolute; inset: 0;
    background: linear-gradient(120deg, #6a6a6a 0%, #2a2a2a 28%, #151515 60%, #0c0c0c 100%);
  }

  /* Front side */
  .card-front { left: 590px; top: 410px; background: var(--paper); }
  .front-edge {
    position: absolute; right: 0; top: 14px;
    width: 12px; height: 60px; background: var(--ink);
  }
  .holder {
    position: absolute; right: 26px; top: 20px; text-align: right; color: var(--ink);
  }
  .holder-name { font: 900 30px/1.1 'Roboto', sans-serif; }
  .holder-role { font: 400 15px/1.3 'Open Sans', sans-serif; margin-top: 2px; }

  .brand {
    position: absolute; left: 30px; top: 144px;
    display: flex; align-items: center; gap: 10px;
  }
  .brand-mark { width: 16px; height: 16px; background: var(--ink); }
  .brand-name {
    font: 700 26px/1 'Roboto', sans-serif; letter-spacing: 12px; color: var(--ink);
  }

  .band {
    position: absolute; left: 0; right: 0; bottom: 0; height: 138px;
    background: var(--band-black);
  }
  .band-art {
    position: absolute; right: 0; top: 90px; width: 180px; height: 230px;
    background: linear-gradient(160deg, #3a3a3a 0%, #111 55%, #000 100%);
    border-top-left-radius: 90px;
  }
  .details {
    position: absolute; left: 30px; top: 196px; width: 330px; color: var(--paper);
    font: 400 14px/1.35 'Open Sans', sans-serif;
  }
  .tagline { margin-bottom: 12px; max-width: 250px; }
  .contact-row { display: flex; align-items: flex-start; gap: 8px; }
  .contact-row svg { flex: none; margin-top: 3px; }
</style>
</head>
<body>
<main class="stage">

  <section class="card card-back" aria-label="Card back">
    <div class="back-pattern" role="img" aria-label="Repeating pattern of small brand symbols in glossy silver fading to black"></div>
  </section>

  <section class="card card-front" aria-label="Card front">
    <div class="front-edge"></div>

    <div class="holder">
      <p class="holder-name">Dalton Pikes</p>
      <p class="holder-role">Founder and CPO</p>
    </div>

    <div class="brand">
      <span class="brand-mark"></span>
      <span class="brand-name">BRIMLEY</span>
    </div>

    <div class="band"></div>
    <div class="band-art" role="img" aria-label="Large black silhouette illustration of an animal with white outline"></div>

    <div class="details">
      <p class="tagline">Chilled coolers and loud speakers...we bring the fun!</p>
      <p class="contact-row">
        <svg width="12" height="12" viewBox="0 0 24 24" aria-hidden="true"><path fill="#fff" d="M6.6 10.8a15 15 0 0 0 6.6 6.6l2.2-2.2a1 1 0 0 1 1-.25 11.4 11.4 0 0 0 3.6.57 1 1 0 0 1 1 1V20a1 1 0 0 1-1 1A17 17 0 0 1 3 4a1 1 0 0 1 1-1h3.5a1 1 0 0 1 1 1c0 1.25.2 2.45.57 3.57a1 1 0 0 1-.25 1z"/></svg>
        <span>555.318.4726</span>
      </p>
      <p class="contact-row">
        <svg width="12" height="14" viewBox="0 0 24 28" aria-hidden="true"><path fill="none" stroke="#fff" stroke-width="2.4" d="M12 2a8 8 0 0 0-8 8c0 6 8 14 8 14s8-8 8-14a8 8 0 0 0-8-8z"/><circle cx="12" cy="10" r="3" fill="#fff"/></svg>
        <span>412 E. Carver Avenue,<br>Ste 2207, Tampa, FL. 33917</span>
      </p>
    </div>
  </section>

</main>
</body>
</html>
```